Wellpath Ledgers New Website

Please review the attached Design Brief with additional details. Thank you!

The goal is to create a website that effectively communicates the benefits of WellPath Ledgers to eye care professionals. The website should streamline the process of understanding and utilizing WellPath Ledgers' services, emphasizing improved patient outcomes, increased referrals, and enhanced patient engagement.

Target Market(s)

Eyecare Professionals

Number of Pages Required

4 page

```html
<!DOCTYPE html>
<html lang="en">
<head>
<meta charset="utf-8">
<title>Wellpath Ledgers</title>
<link rel="stylesheet" href="https://fonts.googleapis.com/css2?family=Roboto:wght@400;500;700&display=swap">
<style>
:root{
  --navy:#14238a;
  --blue:#0a6cf0;
  --orange:#ff8a1c;
  --orange-deep:#ff6d0f;
  --peach:#fff1e0;
  --pale:#eef5fd;
  --text:#555b66;
  --dark:#222;
  --white:#fff;
}
*{box-sizing:border-box;margin:0;padding:0}
html,body{width:1200px;height:4955px;overflow:hidden}
body{font-family:"Roboto",Arial,sans-serif;color:var(--dark);background:var(--white);position:relative}
.abs{position:absolute}
section{position:absolute;left:0;width:1200px;overflow:hidden}

/* header */
.header{top:0;height:90px;background:var(--white);border-top:4px solid var(--orange)}
.brand{left:112px;top:20px;display:flex;align-items:center;gap:8px}
.brand-mark{width:22px;height:22px;background:var(--blue);border-radius:50%}
.brand-name{font-size:21px;font-weight:500;color:var(--navy);line-height:1}
.brand-tag{left:142px;top:58px;font-size:11px;color:var(--navy)}
.call{left:806px;top:0;width:282px;height:40px;background:var(--blue);color:var(--white);font-size:13px;font-weight:500;display:flex;align-items:center;padding-left:40px}
.call-icon{left:808px;top:8px;width:24px;height:24px;border-radius:50%;background:var(--orange)}
.nav{right:112px;top:56px;display:flex;gap:28px;font-size:13px;font-weight:500}
.nav a{color:var(--dark);text-decoration:none}
.nav a.active{color:var(--orange)}
.nav-caret{left:410px;top:44px;width:0;height:0;border-left:8px solid transparent;border-right:8px solid transparent;border-top:8px solid var(--blue)}

/* hero */
.hero{top:90px;height:687px;background:var(--pale)}
.hero h1{left:108px;top:212px;font-size:50px;line-height:60px;font-weight:700;color:var(--navy)}
.hero p{left:110px;top:343px;width:360px;font-size:13px;line-height:21px;color:var(--text)}
.btn{display:inline-flex;align-items:center;gap:6px;background:var(--blue);color:var(--white);font-size:13px;font-weight:700;padding:0 22px;height:40px;text-transform:uppercase;text-decoration:none}
.hero .btn{left:112px;top:422px}
.photo-hero{left:600px;top:142px;width:600px;height:404px;background:linear-gradient(120deg,#dfe7ee,#b9c8d6 50%,#7d8f9c)}
.scroll-down{left:576px;top:660px;width:48px;height:48px;border-radius:50%;background:var(--white);box-shadow:0 4px 14px rgba(0,0,0,.12)}

/* headings */
.sec-title{width:1200px;text-align:center;font-size:42px;font-weight:700;color:var(--navy)}

/* services */
.services{top:777px;height:708px;background:var(--white)}
.service{width:230px}
.service-icon{width:90px;height:90px;border-radius:50%;background:var(--orange);border-top:6px solid var(--blue)}
.service h3{margin-top:24px;font-size:18px;font-weight:500;line-height:24px;color:var(--dark)}
.service p{margin-top:12px;font-size:12px;line-height:21px;color:var(--text)}
.card-lift{padding:0 16px 24px;box-shadow:0 12px 24px rgba(0,0,0,.06)}
.dots{left:566px;top:570px;display:flex;gap:10px}
.dots span{width:14px;height:14px;border-radius:50%;background:#d6dbe3}
.dots span.on{background:var(--blue)}

/* about */
.about{top:1485px;height:818px;background:var(--pale)}
.about h2{left:112px;top:98px;font-size:40px;font-weight:700;color:var(--navy)}
.about .btn{left:930px;top:105px}
.about p{left:111px;top:177px;width:977px;font-size:14px;line-height:26px;color:var(--text);text-align:justify}
.about-circle-blue{left:54px;top:540px;width:210px;height:210px;border-radius:50%;background:var(--blue)}
.about-circle-orange{left:1030px;top:470px;width:95px;height:150px;border-radius:0 80px 80px 0;background:var(--orange)}
.photo-about{left:111px;top:367px;width:977px;height:348px;background:linear-gradient(100deg,#6f8fb2,#b9cbe0 40%,#f3d4a2 70%,#c9a37c);border-radius:6px}

/* benefits */
.benefits{top:2303px;height:692px}
.benefit-label{width:170px;text-align:center}
.benefit-label h4{font-size:13px;font-weight:500;color:var(--dark)}
.benefit-label p{margin-top:8px;font-size:11.5px;line-height:19px;color:var(--text)}
.benefit-band{left:126px;top:307px;width:948px;height:186px;border-radius:93px;background:linear-gradient(90deg,#fde3dd,#ece0f2 25%,#d9f0fb 45%,#feeeda 65%,#e2f1dc 82%,#fde1ea)}

/* pricing */
.pricing{top:2995px;height:600px;background:linear-gradient(90deg,var(--orange-deep),#ffa13d 55%,#ffd786)}
.pricing h2{left:108px;top:205px;font-size:42px;line-height:52px;font-weight:700;color:var(--white)}
.pricing p.lead{left:110px;top:314px;width:310px;font-size:13px;line-height:25px;color:var(--white)}
.plan{top:110px;width:297px;height:380px;background:var(--white);box-shadow:0 8px 24px rgba(0,0,0,.12);text-align:center;padding-top:45px}
.plan h3{font-size:19px;line-height:25px;font-weight:500;color:var(--dark)}
.plan .price{margin-top:10px;font-size:42px;font-weight:700;color:var(--blue)}
.plan .price small{font-size:12px}
.plan ul{list-style:none;margin:22px auto 0;width:200px;text-align:left}
.plan li{font-size:13px;line-height:26px;color:var(--text);display:flex;align-items:center;gap:10px}
.plan li::before{content:"";width:11px;height:11px;border-radius:50%;background:var(--orange)}
.plan .btn{margin-top:22px;width:203px;height:44px;justify-content:center}

/* testimonials */
.testimonials{top:3595px;height:565px}
.quote{left:265px;top:185px;width:670px;text-align:center;font-size:15px;line-height:26px;color:var(--text)}
.quote-mark{font-size:70px;color:#c9cdd4;font-family:Georgia,serif;line-height:1}
.divider{left:225px;top:287px;width:750px;height:1px;background:#d6d9de}
.client{width:1200px;text-align:center}
.arrow{top:263px;width:46px;height:46px;border-radius:50%;border:1.5px solid #444;display:flex;align-items:center;justify-content:center}
.avatar{left:556px;top:386px;width:88px;height:88px;border-radius:50%;border:4px solid var(--orange);background:#8b7b6c}

/* contact */
.contact{top:4160px;height:685px;background:linear-gradient(100deg,#0b5ff0,#0a8ff5 60%,#0a6cf0)}
.contact-panel{left:377px;top:120px;width:711px;height:450px;background:var(--white)}
.contact h2{left:490px;top:150px;font-size:38px;font-weight:700;color:var(--navy)}
.info-card{left:111px;top:135px;width:329px;height:405px;background:var(--orange)}
.info-item{left:150px;display:flex;gap:20px;align-items:flex-start}
.info-icon{width:70px;height:70px;border-radius:50%;background:var(--white);flex:none;display:flex;align-items:center;justify-content:center}
.info-item h4{font-size:15px;font-weight:500;color:var(--white);margin-top:4px}
.info-item p{font-size:11.5px;line-height:18px;color:var(--white);margin-top:6px}
.field{width:250px;border-bottom:1px solid #bfc4cc;font-size:12px;color:#555;padding-bottom:14px}
.contact .btn{left:493px;top:470px}

.footer{top:4845px;height:110px;background:var(--white);text-align:center;font-size:13px;color:var(--dark);padding-top:50px}
</style>
</head>
<body>

<header class="abs header" style="left:0;width:1200px">
  <div class="abs brand"><span class="brand-mark"></span><span class="brand-name">Wellpath Ledgers</span></div>
  <div class="abs brand-tag">Empowering Healthcare</div>
  <div class="abs call">Call Us Today : +1 555 010 2468</div>
  <div class="abs call-icon"></div>
  <span class="abs nav-caret"></span>
  <nav class="abs nav">
    <a class="active" href="#">Home</a><a href="#">About Us</a><a href="#">Services</a><a href="#">Pricing</a><a href="#">Testimonials</a><a href="#">Blog/News</a><a href="#">Contact Us</a><a href="#">FAQs</a>
  </nav>
</header>

<section class="hero">
  <div class="abs" style="left:-80px;top:-110px;width:260px;height:260px;border-radius:50%;background:#e1e9f2"></div>
  <div class="abs" style="left:290px;top:-10px;width:830px;height:830px;border-radius:50%;background:var(--peach)"></div>
  <div class="abs" style="left:830px;top:380px;width:330px;height:330px;border-radius:50%;background:#dfe8f4"></div>
  <div class="abs" style="left:967px;top:78px;width:121px;height:80px;background:var(--blue);border-radius:6px 6px 0 0"></div>
  <div class="abs" style="left:967px;top:530px;width:121px;height:87px;background:var(--blue);border-radius:0 0 6px 6px"></div>
  <h1 class="abs">WellPath<br>Ledgers</h1>
  <p class="abs">Lorem ipsum dolor sit amet, consectetur adipiscing elit, sed do eiusmod tempor incididunt ut labore et dolore magna aliqua.</p>
  <a class="abs btn" href="#">Get Started <svg width="8" height="10" viewBox="0 0 8 10"><path d="M2 1l4 4-4 4" stroke="#fff" stroke-width="2" fill="none"/></svg></a>
  <div class="abs photo-hero" role="img" aria-label="Photo of a clinician reviewing a clipboard with a senior patient"></div>
  <div class="abs scroll-down"><svg width="48" height="48" viewBox="0 0 48 48"><path d="M18 19l6 5 6-5M18 25l6 5 6-5" stroke="#222" stroke-width="2" fill="none"/></svg></div>
</section>

<section class="services">
  <h2 class="abs sec-title" style="top:115px">Our Services</h2>
  <div class="abs service" style="left:107px;top:222px">
    <div class="service-icon"></div>
    <h3>Diabetes Management Registry</h3>
    <p>This registry will enhance your care of diabetic patients by monitoring HbA1c change and predicting the advent of a retinopathy.</p>
  </div>
  <div class="abs service card-lift" style="left:345px;top:222px;width:262px">
    <div class="service-icon"></div>
    <h3>Cataract Extraction Registry</h3>
    <p>Evaluating outcomes from cataract surgery is a very complex issue that involves many different factors. The data from the cataract</p>
  </div>
  <div class="abs service" style="left:615px;top:222px">
    <div class="service-icon"></div>
    <h3>Dry Eye Registry</h3>
    <p>This registry will guide you in prescribing the most effective treatment modalities for specific types of dry eye patients.</p>
  </div>
  <div class="abs service" style="left:869px;top:222px">
    <div class="service-icon"></div>
    <h3>Myopia Registry</h3>
    <p>Data driven reports from this registry, will guide you in prescribing the most efficacious modality of myopia management for each</p>
  </div>
  <div class="abs dots"><span></span><span class="on"></span><span></span></div>
</section>

<section class="about">
  <h2 class="abs">About The Registry</h2>
  <a class="abs btn" href="#">Learn More <svg width="8" height="10" viewBox="0 0 8 10"><path d="M2 1l4 4-4 4" stroke="#fff" stroke-width="2" fill="none"/></svg></a>
  <p class="abs">WellPath Ledgers can guide your clinical decision making by providing you with “real-time” clinical outcome analytics. The analytics are designed to look at practical issues affecting the quality of care you deliver to your patients. These issues impact the efficiency and viability of your practice. There are various types of registries which can be used in different ways. Some registries are known as “Reporting Registries” which are designed to report merit-based incentive payment systems (MIPS) scores. In comparison, WellPath Ledgers is a “Clinical Outcome Registry” that creates clinical outcome analytics. Most areas of Medicine have been utilizing registries for many years, one example is the Northland Heart Society’s National Cardiac Data Ledger.</p>
  <div class="abs about-circle-blue"></div>
  <div class="abs about-circle-orange"></div>
  <div class="abs photo-about" role="img" aria-label="Photo of a person filling in a patient information form on a laptop"></div>
</section>

<section class="benefits">
  <h2 class="abs sec-title" style="top:105px">Our Benefits</h2>
  <div class="abs benefit-label" style="left:275px;top:205px"><h4>Duis aute irure</h4><p>Lorem ipsum dolor sit amet, consectetur adipiscing</p></div>
  <div class="abs benefit-label" style="left:593px;top:205px"><h4>Duis aute irure</h4><p>Lorem ipsum dolor sit amet, consectetur adipiscing</p></div>
  <div class="abs benefit-label" style="left:912px;top:205px"><h4>Duis aute irure</h4><p>Lorem ipsum dolor sit amet, consectetur adipiscing</p></div>
  <div class="abs benefit-band" role="img" aria-label="Decorative chain of six coloured rings, each holding a benefit icon"></div>
  <div class="abs benefit-label" style="left:115px;top:500px"><h4>Duis aute irure</h4><p>Lorem ipsum dolor sit amet, consectetur adipiscing</p></div>
  <div class="abs benefit-label" style="left:434px;top:500px"><h4>Duis aute irure</h4><p>Lorem ipsum dolor sit amet, consectetur adipiscing</p></div>
  <div class="abs benefit-label" style="left:753px;top:500px"><h4>Duis aute irure</h4><p>Lorem ipsum dolor sit amet, consectetur adipiscing</p></div>
</section>

<section class="pricing">
  <h2 class="abs">Choose Pricing<br>Plans</h2>
  <p class="abs lead">Lorem ipsum dolor sit amet, consectetur adipiscing elit, sed do eiusmod tempor incididunt ut labore et dolore magna aliqua.</p>
  <div class="abs plan" style="left:465px">
    <h3>Initial One-Time<br>Setup</h3>
    <div class="price">1,000<small>US$</small></div>
    <ul><li>Lorem ipsum dolor sit amet</li><li>Lorem ipsum dolor sit amet</li><li>Lorem ipsum dolor sit amet</li><li>Lorem ipsum dolor sit amet</li></ul>
    <a class="btn" href="#">Subscribe</a>
  </div>
  <div class="abs plan" style="left:791px">
    <h3>Monthly<br>Subscription</h3>
    <div class="price">99<small>US$</small></div>
    <ul><li>Lorem ipsum dolor sit amet</li><li>Lorem ipsum dolor sit amet</li><li>Lorem ipsum dolor sit amet</li><li>Lorem ipsum dolor sit amet</li></ul>
    <a class="btn" href="#">Subscribe</a>
  </div>
</section>

<section class="testimonials">
  <h2 class="abs sec-title" style="top:95px">Testimonials</h2>
  <div class="abs quote-mark" style="left:230px;top:150px">“</div>
  <p class="abs quote">Working with WellPath Ledgers is the best investment that I have ever made in my practices. Access to my clinical outcome data help build pcp referrals. Actually, in one day, I received 40 new diabetic referrals.</p>
  <div class="abs quote-mark" style="left:818px;top:240px">”</div>
  <div class="abs divider"></div>
  <div class="abs client" style="top:302px;font-size:20px;font-weight:500">Dr. Miles Harlan OD</div>
  <div class="abs client" style="top:338px;font-size:15px;color:var(--text)">Riverbend Eye, Oakdale, Tennessee</div>
  <div class="abs avatar" role="img" aria-label="Client portrait"></div>
  <div class="abs arrow" style="left:65px"><svg width="12" height="14" viewBox="0 0 12 14"><path d="M8 2L3 7l5 5" stroke="#333" stroke-width="2" fill="none"/></svg></div>
  <div class="abs arrow" style="left:1087px"><svg width="12" height="14" viewBox="0 0 12 14"><path d="M4 2l5 5-5 5" stroke="#333" stroke-width="2" fill="none"/></svg></div>
</section>

<section class="contact">
  <div class="abs" style="left:-200px;top:-40px;width:560px;height:560px;border-radius:50%;background:rgba(255,255,255,.07)"></div>
  <div class="abs" style="left:1000px;top:470px;width:320px;height:320px;border-radius:50%;background:rgba(0,40,200,.25)"></div>
  <div class="abs contact-panel"></div>
  <div class="abs info-card"></div>
  <div class="abs info-item" style="top:175px"><div class="info-icon"><svg width="26" height="30" viewBox="0 0 26 30"><path d="M13 28s-10-10-10-16a10 10 0 0 1 20 0c0 6-10 16-10 16z" stroke="var(--orange)" stroke-width="2" fill="none"/><circle cx="13" cy="12" r="4" stroke="var(--orange)" stroke-width="2" fill="none"/></svg></div><div><h4>Address</h4><p>122,Lorem ipsum dolor<br>amet, consec</p></div></div>
  <div class="abs info-item" style="top:290px"><div class="info-icon"><svg width="30" height="24" viewBox="0 0 30 24"><rect x="2" y="3" width="26" height="18" rx="2" stroke="var(--orange)" stroke-width="2" fill="none"/><path d="M3 4l12 9 12-9" stroke="var(--orange)" stroke-width="2" fill="none"/></svg></div><div><h4>Email Address</h4><p>info@wellpathledgers.com</p></div></div>
  <div class="abs info-item" style="top:405px"><div class="info-icon"><svg width="28" height="28" viewBox="0 0 28 28"><path d="M6 3l5 1 2 6-3 2a14 14 0 0 0 6 6l2-3 6 2 1 5c-1 2-3 3-5 3C11 27 1 17 1 8c0-2 2-4 5-5z" stroke="var(--orange)" stroke-width="2" fill="none"/></svg></div><div><h4>Phone</h4><p>+1 555 010 2468</p></div></div>
  <h2 class="abs">Contact Us</h2>
  <div class="abs field" style="left:493px;top:235px">First name</div>
  <div class="abs field" style="left:767px;top:235px">Last name</div>
  <div class="abs field" style="left:493px;top:296px">Email</div>
  <div class="abs field" style="left:767px;top:296px">Phone</div>
  <div class="abs field" style="left:493px;top:365px;width:520px;padding-bottom:45px">Write your message here...</div>
  <a class="abs btn" href="#">Submit Now <svg width="8" height="10" viewBox="0 0 8 10"><path d="M2 1l4 4-4 4" stroke="#fff" stroke-width="2" fill="none"/></svg></a>
</section>

<footer class="abs footer" style="left:0;width:1200px">© Copyrights 2023 | All Rights Reserved</footer>

</body>
</html>
```